Suds Haven Laundromat Wordpress Design

We need a Wordpress website design for our laundromat, Suds Haven Atlanta, at www.sudshavenatlanta-example.com. We would like to have 6 pages: Home, About Us, Services, Locations, Reviews and Contact us. We will provide content for the text on each page. What we do: We are a full service laundromat that provides dry cleaning drop off, professional laundry services, wash dry fold and self service laundry to the local community. We would like to use the color scheme from our logo to convey a warm, safe, and bright business that caters to its diverse community.
Updates

I like the structure of this laundromat website: http://www.washtroveusa-example.com/ Using my logo and color scheme in the above referenced website is what. Am looking for. The photos attached to the project with the female model should be used as a primary focus and supplemented by actual photos of the equipment.

Target Market(s)

Our target market is a diverse group of people from Midtown Atlanta - LGBTQ community /Locals/Regulars that have been coming to laundromat for 30 years.

Industry/Entity Type

Laundromat

Coding

Coded - Design and coding required

Number of Pages Required

5+ page

Font styles to use
Sans Serif

Colors
0054AA
0677BA
7BADD7
CADEEF
E8F1F8

Requirements
Must have
• Feature this video on the main page: https://videohost-example.com/xq7Rm2bPz4k

```html
<!DOCTYPE html>
<html lang="en">
<head>
<meta charset="utf-8">
<title>Services | Suds Haven Laundromat</title>
<link href="https://fonts.googleapis.com/css2?family=Bebas+Neue&family=Montserrat:wght@400;500;600&display=swap" rel="stylesheet">
<style>
  :root {
    --brand-blue: #0054aa;
    --accent-blue: #0677ba;
    --sky-blue: #1ea0dd;
    --pale-blue: #cadeef;
    --mist: #eef3f7;
    --ink: #222831;
    --body-text: #3c4148;
    --footer-bg: #324868;
    --footer-text: #e7edf5;
    --rule: #e3e8ee;
  }
  * { box-sizing: border-box; margin: 0; padding: 0; }
  html, body { width: 1200px; height: 2285px; overflow: hidden; background: #fff; }
  body { position: relative; font-family: "Montserrat", sans-serif; color: var(--body-text); }

  .site-header { position: absolute; top: 0; left: 0; width: 1200px; height: 75px; background: #fff; z-index: 2; }
  .brand { position: absolute; left: 104px; top: 20px; display: flex; align-items: center; gap: 8px; }
  .brand-dot { width: 22px; height: 22px; border-radius: 50%; background: var(--sky-blue); }
  .brand-name { font-family: "Montserrat", sans-serif; font-weight: 600; font-size: 26px; color: var(--brand-blue); }
  .main-nav a { position: absolute; top: 33px; font-size: 12.5px; color: var(--ink); text-decoration: none; letter-spacing: .2px; }
  .main-nav a.is-active { font-weight: 600; }
  .main-nav a.is-active::after { content: ""; position: absolute; left: 0; right: 0; top: 38px; height: 4px; background: var(--brand-blue); }
  .nav-divider { position: absolute; left: 1029px; top: 19px; width: 2px; height: 38px; background: var(--brand-blue); }
  .header-social { position: absolute; top: 31px; width: 12px; height: 12px; border-radius: 50%; background: var(--ink); }

  .hero { position: absolute; top: 75px; left: 0; width: 1200px; height: 420px; }
  .hero-photo { position: absolute; inset: 0; background: linear-gradient(100deg, #d9d9d2 0%, #c5c8c2 30%, #b4bcbc 50%, #8a8f91 75%, #6f7578 100%); }
  .hero-curve { position: absolute; inset: 0; }

  .breadcrumb { position: absolute; top: 504px; left: 163px; font-size: 12.5px; color: var(--ink); }
  .breadcrumb .current { color: var(--brand-blue); font-weight: 500; }

  .section-title { position: absolute; top: 596px; left: 0; width: 1200px; text-align: center; font-family: "Bebas Neue", sans-serif; font-size: 36px; color: var(--ink); letter-spacing: .5px; }
  .section-title span { color: var(--brand-blue); }
  .title-bar { position: absolute; top: 641px; left: 578px; width: 44px; height: 2px; background: var(--sky-blue); }

  .service-art { position: absolute; width: 165px; height: 165px; border-radius: 50%; background: var(--mist); }
  .service-text { position: absolute; }
  .service-name { font-family: "Bebas Neue", sans-serif; font-size: 27px; color: var(--accent-blue); letter-spacing: .3px; line-height: 1; margin-bottom: 12px; }
  .service-text p { font-size: 12.6px; line-height: 24.4px; color: var(--body-text); }
  .service-text p + p { margin-top: 8px; }
  .service-rule { position: absolute; left: 216px; width: 782px; border-top: 1px dashed var(--rule); }

  .cta-button { position: absolute; top: 1641px; left: 524px; width: 150px; height: 41px; background: var(--sky-blue); color: #fff; font-size: 12.5px; font-weight: 600; display: flex; align-items: center; justify-content: center; text-decoration: none; }

  .site-footer { position: absolute; top: 1758px; left: 0; width: 1200px; height: 527px; background: var(--footer-bg); color: var(--footer-text); }
  .footer-brand { position: absolute; top: 98px; left: 0; width: 1200px; display: flex; justify-content: center; align-items: center; gap: 12px; }
  .footer-brand .brand-dot { width: 30px; height: 30px; background: #fff; }
  .footer-brand .brand-name { font-size: 44px; color: #fff; }
  .footer-rule { position: absolute; height: 1px; background: rgba(255,255,255,.14); }
  .footer-nav a { position: absolute; top: 231px; font-size: 15px; color: #fff; text-decoration: none; }
  .footer-social { position: absolute; top: 225px; width: 30px; height: 30px; border-radius: 50%; background: #fff; }
  .footer-contact { position: absolute; top: 305px; font-size: 14px; line-height: 24px; }
  .contact-icon { position: absolute; }
  .delivery-note { color: var(--sky-blue); }
  .copyright { position: absolute; top: 462px; left: 0; width: 1200px; text-align: center; font-size: 12.5px; color: var(--footer-text); }
  .copyright strong { font-weight: 600; color: #fff; }
</style>
</head>
<body>

<header class="site-header">
  <div class="brand"><span class="brand-dot"></span><span class="brand-name">Suds Haven</span></div>
  <nav class="main-nav">
    <a href="#" style="left:416px">HOME</a>
    <a href="#" style="left:497px">ABOUT US</a>
    <a href="#" class="is-active" style="left:604px">SERVICES</a>
    <a href="#" style="left:709px">LOCATION</a>
    <a href="#" style="left:826px">REVIEWS</a>
    <a href="#" style="left:925px">CONTACT US</a>
  </nav>
  <span class="nav-divider"></span>
  <span class="header-social" style="left:1048px"></span>
  <span class="header-social" style="left:1073px"></span>
</header>

<section class="hero">
  <div class="hero-photo" role="img" aria-label="Interior of the laundromat with rows of white and stainless steel front-loading washers and potted plants"></div>
  <svg class="hero-curve" width="1200" height="420" viewBox="0 0 1200 420">
    <path d="M0,329 Q600,445 1200,324 L1200,420 L0,420 Z" fill="#fff"/>
    <path d="M0,332 Q580,462 1150,349 Q590,478 0,348 Z" fill="#0054aa"/>
  </svg>
</section>

<div class="breadcrumb">HOME / <span class="current">SERVICES</span></div>

<h1 class="section-title">Our <span>Services</span></h1>
<span class="title-bar"></span>

<div class="service-art" style="left:236px;top:681px" role="img" aria-label="Line icon of a shirt on a hanger"></div>
<div class="service-text" style="left:425px;top:698px;width:545px">
  <h2 class="service-name">Wash Dry Fold</h2>
  <p>Tired, too much to do, own a business and need linens, sheets, towels, etc., cleaned? Don't worry, we can do your laundry for you! Have your laundry expertly washed, dried, and folded how you want it, we can even provide same day service. We also offer discounts for large orders.</p>
</div>
<div class="service-rule" style="top:879px"></div>

<div class="service-text" style="left:238px;top:944px;width:518px">
  <h2 class="service-name">Professional Laundry Services</h2>
  <p>If you want to enjoy the perks of dry cleaning without all the chemicals, we offer a wash, dry, and press/iron service. &nbsp;You can relax knowing that your clothes will be flawlessly cleaned.</p>
</div>
<div class="service-art" style="left:785px;top:914px" role="img" aria-label="Line icon of a washing machine, ironing board and hangers"></div>
<div class="service-rule" style="top:1111px"></div>

<div class="service-art" style="left:236px;top:1147px" role="img" aria-label="Line icon of a dry cleaning attendant with a garment"></div>
<div class="service-text" style="left:425px;top:1178px;width:545px">
  <h2 class="service-name">Dry Cleaning Drop Off</h2>
  <p>Do you have clothing or linens that are made from delicate fabrics that aren't machine washable? We offer professional dry-cleaning services for our customers and businesses.</p>
</div>
<div class="service-rule" style="top:1345px"></div>

<div class="service-text" style="left:238px;top:1393px;width:540px">
  <h2 class="service-name">Self Service Laundry</h2>
  <p>With over 40 well maintained self-service washers and dryers laundry will be a thing of the past! We now have CoinTap a free app. you download on your phone making quarters obsolete. Whether you need to wash a comforter or a load of baby clothes we have a working machine for you, so you can finish your laundry quickly!</p>
  <p>Meanwhile, you can relax in a clean and cared for environment. We offer free WiFi, arcade and vending machines, soap machines, plenty of parking, and there are some great restaurants in the mall we are located in.</p>
</div>
<div class="service-art" style="left:785px;top:1381px" role="img" aria-label="Line icon of a clean washing machine with folded towels"></div>

<a class="cta-button" href="#">Contact Us Today</a>

<footer class="site-footer">
  <div class="footer-brand"><span class="brand-dot"></span><span class="brand-name">Suds Haven</span></div>
  <div class="footer-rule" style="top:199px;left:293px;width:612px"></div>
  <nav class="footer-nav">
    <a href="#" style="left:254px">Home</a>
    <a href="#" style="left:338px">About Us</a>
    <a href="#" style="left:446px">Services</a>
    <a href="#" style="left:549px">Location</a>
    <a href="#" style="left:659px">Reviews</a>
    <a href="#" style="left:762px">Contact Us</a>
  </nav>
  <span class="footer-social" style="left:879px"></span>
  <span class="footer-social" style="left:924px"></span>
  <div class="footer-rule" style="top:280px;left:240px;width:720px"></div>

  <svg class="contact-icon" style="left:245px;top:306px" width="20" height="20" viewBox="0 0 20 20" fill="none" stroke="#e7edf5" stroke-width="1.2">
    <circle cx="9" cy="11" r="7.5"/><path d="M1.5,11 H16.5 M9,3.5 C5,8 5,14 9,18.5 M9,3.5 C13,8 13,14 9,18.5"/>
    <circle cx="15" cy="5" r="3.2" fill="#324868"/><circle cx="15" cy="5" r="1"/>
  </svg>
  <div class="footer-contact" style="left:277px;width:320px">Brookfield Plaza, 2210 Magnolia Ave NE., # 118, Atlanta, GA 30399</div>
  <svg class="contact-icon" style="left:245px;top:366px" width="18" height="18" viewBox="0 0 18 18" fill="none" stroke="#e7edf5" stroke-width="1.2">
    <path d="M4,1.5 L7,5 L5.5,7 C6.5,9.5 8.5,11.5 11,12.5 L13,11 L16.5,14 L14.5,16.5 C8,16 2,10 1.5,3.5 Z"/>
  </svg>
  <div class="footer-contact" style="left:275px;top:364px">(404) 555-0142</div>

  <div class="footer-contact" style="left:611px;width:400px">
    <div class="delivery-note">Delivery Available* please contact us for details</div>
    <div style="margin-top:8px">Covid 19 hours - open 7 days a week 8 am to 8 pm<br>Last wash begins 6:30 pm</div>
  </div>

  <div class="footer-rule" style="top:417px;left:161px;width:879px"></div>
  <p class="copyright">Copyright © 2021 <strong>Suds Haven Atlanta</strong>. All Rights Reserved.</p>
</footer>

</body>
</html>
```